Foot and ankle surgeon requires a website design

I need a website where prospective and established patients can obtain information and then direct them to making appointments. My practice is a highly professional surgical practice specialising in surgery to the foot and ankle. My title is Mr Colin Brasket, Podiatric Foot & Ankle Surgeon. My qualifications are: BSc MSc FACPS
The practice website will require information on: Locations, phone numbers to make appointments, general background on podiatric surgery,
I would like to include information on: my hospital appointments, surgical fellowships held, training programs undertaken, association memberships, publications written, links to useful websites
A page dedicated to common foot conditions would be useful and also a page with referral information including an online registration section that will be sent direct to the receptionist.
Examples of similar websites include:
http://www.dorvelquintaro.com.au/
http://www.haldenfootsurgeon.com.au/
I will provide files on logo, self photos and my personal training history etc.
Also if there is going to be a background theme I personally am associated with surfing and beach activities, it would be great if this was able to be reflected in the design.
Thank you.

```html
<!DOCTYPE html>
<html lang="en">
<head>
<meta charset="utf-8">
<title>Mr Colin Brasket – Podiatric Foot &amp; Ankle Surgeon</title>
<link rel="stylesheet" href="https://fonts.googleapis.com/css2?family=Tinos:wght@400;700&family=PT+Sans:wght@400;700&family=Arimo:wght@400;700&family=Montserrat:wght@400;700&display=swap">
<style>
  :root {
    --sky-top: #cdeaf6;
    --sky-bottom: #e6f5fb;
    --navy: #1b4a7a;
    --navy-dark: #123a63;
    --orange: #f07a23;
    --orange-dark: #e0611a;
    --text: #555b60;
    --text-dark: #222;
    --teal-text: #2b5660;
    --panel: #c4e6f3;
    --white: #ffffff;
    --line: #c9ced2;
  }
  * { box-sizing: border-box; margin: 0; padding: 0; }
  html, body { width: 1001px; height: 1200px; overflow: hidden; }
  body {
    position: relative;
    background: linear-gradient(180deg, var(--sky-top) 0%, var(--sky-bottom) 45%, var(--sky-top) 100%);
    font-family: "PT Sans", sans-serif;
    color: var(--text);
  }
  .abs { position: absolute; }
  h1, h2, h3 { font-weight: 400; white-space: nowrap; }

  /* Header */
  .brand { left: 92px; top: 64px; display: flex; align-items: center; gap: 10px; }
  .brand-mark { width: 34px; height: 34px; border-radius: 50%; background: var(--orange); }
  .brand-name { font-family: "Tinos", serif; font-weight: 700; font-size: 19px; color: var(--navy); line-height: 1; }
  .brand-sub { font-family: "Tinos", serif; font-weight: 700; font-size: 10px; color: var(--navy); margin-top: 3px; }
  .header-cta { right: 92px; top: 46px; text-align: right; font-family: "Montserrat", sans-serif; }
  .book-link { font-size: 18px; color: var(--navy); }
  .call { margin-top: 10px; display: flex; align-items: center; justify-content: flex-end; gap: 8px; font-size: 16px; color: var(--navy); font-weight: 700; }
  .call-num { font-size: 20px; color: #555; letter-spacing: 1px; }

  /* Nav */
  .main-nav { left: 83px; top: 144px; width: 834px; height: 37px; border-radius: 6px 6px 0 0;
    background: linear-gradient(180deg, #f58a35, var(--orange-dark)); display: flex; }
  .main-nav a { font-family: "Arimo", sans-serif; font-size: 12px; color: var(--white); text-decoration: none;
    display: flex; align-items: center; justify-content: center; border-right: 1px solid #c95413; }
  .main-nav a:last-child { border-right: none; flex: 1; }

  /* Hero */
  .hero { left: 83px; top: 181px; width: 834px; height: 340px;
    background: linear-gradient(120deg, #f2eeea 0%, #e8d3c2 35%, #b77a55 60%, #8a5a3e 80%, #e9e6e3 100%); }
  .hero-card { left: 95px; top: 240px; width: 369px; height: 177px; background: rgba(245,245,245,0.88); padding: 14px 16px; }
  .hero-title { font-family: "Tinos", serif; font-size: 33px; color: var(--navy); line-height: 1.1; }
  .hero-sub { font-family: "Tinos", serif; font-size: 23px; color: var(--orange); margin-top: 4px; white-space: nowrap; }
  .hero-text { font-size: 11px; color: #333; line-height: 16.5px; margin-top: 9px; }

  /* Content sheet */
  .sheet { left: 83px; top: 521px; width: 834px; height: 572px; background: var(--white); box-shadow: 0 1px 3px rgba(0,0,0,0.15); }
  .welcome-title { left: 96px; top: 546px; font-family: "Tinos", serif; font-size: 24px; color: var(--navy); }
  .welcome-text { left: 97px; top: 586px; width: 508px; font-size: 11px; line-height: 19.3px; text-align: justify; }
  .welcome-strong { left: 97px; top: 690px; width: 508px; font-size: 11px; line-height: 19.3px; color: var(--text-dark); }
  .service-list { left: 100px; top: 750px; list-style: none; font-size: 13.5px; color: var(--teal-text); }
  .service-list li { height: 30.5px; }
  .service-list li::before { content: "»"; margin-right: 7px; }
  .surgery-photo { left: 434px; top: 747px; width: 171px; height: 110px; background: linear-gradient(135deg, #2f8b8a, #6fb7b0 50%, #1f4c55); }

  /* Appointment panel */
  .appt { left: 627px; top: 547px; width: 275px; height: 312px; background: var(--panel); border-radius: 8px; }
  .appt-title { left: 649px; top: 562px; font-family: "Tinos", serif; font-weight: 700; font-size: 24px; color: var(--navy); }
  .field { background: var(--white); font-family: "Arimo", sans-serif; font-size: 12px; color: #888; padding-left: 8px; display: flex; align-items: center; }
  .label { font-family: "Arimo", sans-serif; font-size: 11.5px; color: #333; }
  .select { background: var(--white); border: 1px solid #d3e4ea; border-radius: 4px; font-family: "Arimo", sans-serif; font-size: 11.5px; color: #888;
    display: flex; align-items: center; justify-content: space-between; padding: 0 6px 0 9px; }
  .select::after { content: "⬍"; font-size: 10px; color: #333; }
  .btn-book { left: 650px; top: 806px; width: 217px; height: 32px; border-radius: 7px; background: linear-gradient(180deg, #f78d3c, var(--orange-dark));
    color: var(--white); font-family: "Montserrat", sans-serif; font-weight: 700; font-size: 17px; letter-spacing: 1px; display: flex; align-items: center; justify-content: center; }

  /* Conditions */
  .cond-title { left: 100px; top: 902px; font-family: "Tinos", serif; font-size: 24px; color: var(--navy); }
  .cond-rule { left: 377px; top: 921px; width: 494px; height: 1px; background: var(--line); }
  .cond-card { top: 957px; width: 160px; }
  .cond-photo { height: 90px; border-radius: 8px; background: linear-gradient(180deg, #e9e2de, #c89583 60%, #a86f5b); }
  .cond-name { text-align: center; font-family: "Arimo", sans-serif; font-size: 13.5px; color: var(--navy); margin-top: 10px; }
  .arrow { top: 985px; }

  /* Footer */
  .footer-links { left: 90px; top: 1124px; font-family: "Arimo", sans-serif; font-size: 11px; color: #333; display: flex; gap: 15px; }
  .copyright { left: 90px; top: 1147px; font-family: "Arimo", sans-serif; font-size: 11px; color: #333; }
  .social { top: 1121px; width: 44px; height: 44px; border-radius: 50%; }
</style>
</head>
<body>

<header>
  <div class="abs brand">
    <span class="brand-mark"></span>
    <div>
      <div class="brand-name">Mr Colin Brasket</div>
      <div class="brand-sub">Podiatric Foot &amp; Ankle Surgeon</div>
    </div>
  </div>
  <div class="abs header-cta">
    <div class="book-link">Book An Online Appintment</div>
    <div class="call">
      <svg width="23" height="23" viewBox="0 0 24 24" aria-hidden="true">
        <circle cx="12" cy="12" r="12" fill="#f07a23"/>
        <path d="M8.2 6.5c.5-.3 1.1-.2 1.4.3l1 1.7c.3.5.2 1.1-.3 1.4l-.7.5c.6 1.4 1.6 2.5 3 3.2l.5-.7c.3-.5.9-.6 1.4-.3l1.7 1c.5.3.6.9.3 1.4l-.6.9c-.5.7-1.4 1-2.2.7-3-1.1-5.300-3.4-6.4-6.4-.3-.8 0-1.7.7-2.2z" fill="#fff"/>
      </svg>
      <span>Call Now !!</span><span class="call-num">08 9000 4417</span>
    </div>
  </div>
</header>

<nav class="abs main-nav">
  <a href="#" style="width:79px">HOME</a>
  <a href="#" style="width:86px">ABOUT</a>
  <a href="#" style="width:100px">PATIENTS</a>
  <a href="#" style="width:161px">PODIATRIC SURGERY</a>
  <a href="#" style="width:133px">APPOINTMENTS</a>
  <a href="#" style="width:75px">BLOG</a>
  <a href="#" style="width:73px">FAQ</a>
  <a href="#">CONTACT US</a>
</nav>

<section>
  <div class="abs hero" role="img" aria-label="Photo of hands massaging a patient's foot and ankle on a towel"></div>
  <div class="abs hero-card">
    <h1 class="hero-title">MR.COLIN BRASKET</h1>
    <div class="hero-sub">Podiatric Foot &amp; Ankle Surgeon</div>
    <p class="hero-text">Lorem ipsum dolor sit amet, consectetuer adipiscing elit, sed diam nonummy nibh euismod tincidunt ut laoreet dolore magna aliquam erat volutpat.</p>
  </div>
</section>

<main>
  <div class="abs sheet"></div>

  <h2 class="abs welcome-title">Welcome to Mr Colin Brasket</h2>
  <p class="abs welcome-text">Maecenas tempor, justo id luctus fringilla, nunc ipsum gravida metus, vel tincidunt elit ligula vel dui. Sed eu gravida quam. Aenean tempus, leo at tristique consectetur, elit tortor scelerisque leo, sed sagittis nisl nisl sit amet libero. Curabitur ac libero arcu. Pellentesque adipiscing ultricies consectetur. Donec ullamcorper nunc orci, nec sagittis lectus varius vitae. Sed pharetra enim ac dapibus congue.Etiam egestas imperdiet tellus facilisis luctus. Proin porta justo felis, eget lobortis ligula placerat quis.</p>
  <p class="abs welcome-strong">Sed convallis accumsan nunc, nec tempus sapien venenatis sed. Etiam id scelerisque turpis, et volutpat metus. Praesent semper diam ut magna sollicitudin, at facilisis ante sodales.</p>
  <ul class="abs service-list">
    <li>Network Design and installation</li>
    <li>PC support</li>
    <li>Custom application design and implementation</li>
  </ul>
  <div class="abs surgery-photo" role="img" aria-label="Photo of a surgical team operating in theatre"></div>

  <aside>
    <div class="abs appt"></div>
    <h3 class="abs appt-title">Hopital Appointments</h3>
    <div class="abs field" style="left:651px;top:606px;width:217px;height:30px">Name</div>
    <div class="abs field" style="left:651px;top:644px;width:217px;height:29px">Contact Number</div>
    <div class="abs label" style="left:653px;top:682px">Preferred Date?</div>
    <div class="abs select" style="left:653px;top:705px;width:53px;height:25px">Day</div>
    <div class="abs select" style="left:714px;top:705px;width:90px;height:25px">Month</div>
    <div class="abs label" style="left:653px;top:741px">Preferred Time?</div>
    <div class="abs select" style="left:653px;top:761px;width:54px;height:25px">12</div>
    <div class="abs select" style="left:715px;top:761px;width:56px;height:25px">00</div>
    <div class="abs select" style="left:780px;top:761px;width:54px;height:25px">am</div>
    <div class="abs btn-book">Request Booking</div>
  </aside>

  <h2 class="abs cond-title">Common Foot Conditions</h2>
  <div class="abs cond-rule"></div>

  <svg class="abs arrow" style="left:97px" width="14" height="30" viewBox="0 0 14 30" aria-hidden="true"><path d="M12 2 L3 15 L12 28" fill="none" stroke="#9aa3a8" stroke-width="2"/></svg>
  <svg class="abs arrow" style="left:884px" width="14" height="30" viewBox="0 0 14 30" aria-hidden="true"><path d="M2 2 L11 15 L2 28" fill="none" stroke="#9aa3a8" stroke-width="2"/></svg>

  <div class="abs cond-card" style="left:129px">
    <div class="cond-photo" role="img" aria-label="Photo of a foot in a post-operative boot"></div>
    <div class="cond-name" style="margin-top:8px">Ankle Replacement</div>
  </div>
  <div class="abs cond-card" style="left:322px">
    <div class="cond-photo" role="img" aria-label="Photo of a pair of bare feet"></div>
    <div class="cond-name">Ankle Trauma</div>
  </div>
  <div class="abs cond-card" style="left:515px">
    <div class="cond-photo" role="img" aria-label="Photo of a foot in a post-operative boot"></div>
    <div class="cond-name">Tendom Rupture</div>
  </div>
  <div class="abs cond-card" style="left:705px">
    <div class="cond-photo" role="img" aria-label="Photo of a pair of bare feet"></div>
    <div class="cond-name">Ankle Pain</div>
  </div>
</main>

<footer>
  <div class="abs footer-links">
    <span>Home</span><span>|</span><span>About</span><span>|</span><span>Patients</span><span>|</span><span>Podiatric Surgery</span><span>|</span><span>Appointments</span><span>|</span><span>Blog</span><span>|</span><span>FAQ</span>
  </div>
  <div class="abs copyright">Copyright © 2014 Mr Colin Brasket. All rights reserved.</div>
  <span class="abs social" style="left:706px;background:#0d3f6b"></span>
  <span class="abs social" style="left:759px;background:#1ea1e6"></span>
  <span class="abs social" style="left:814px;background:#f39c12"></span>
  <span class="abs social" style="left:866px;background:#b5b8ba"></span>
</footer>

</body>
</html>
```